Website for a company offering full serivce charging solutions for electric cars

The company "tanu-werk" (english: "tanu-works") offering all-in-one-solutions for charging infrastructure for electric mobility.

There are four products:
1- Wallboxes for single-family homes
2- Solutions for property devloper/-management for property parking space
3- All-in-one-charging solution for municipalities/communities
4- Solutions for tourism/hotels/holiday appartments

The Website structure:
1. Main Page
2.1. Product Page Single Homes
2.2. Product Page Property Management / Parking
2.3. Product Page Municipality
2.4. Product Page Tourism
3. Contact Form / Request for information
4. Imprint / Legal

The Website should be built on Wordpress with a powerful possibility to simply add/modify specific landing pages.

We would like you to implement the website later and also maintain it if possible, but we would be able to do minor modifications by ourselfs (for A/B-Testing)

The website should be clear and simple, easy to understand.
Target group is mainly B2C without deeper knowledge of that topic.

It should suggest, that we will provide a very simple way to get the charging infrastructure done.

We need a contact form, maybe we will use Hubspot later.

Attached you will find a draft of the main page and a landing page (for 2.2) - it is just the content, please ignore the design. We would love to let you create a suitable design.
Also you will find some drafts a bit different for the same story.

I added also a few stock photos, but they don't need to be used! If you have better ideas, you are welcome!

Industry/Entity Type

Charging/Electric mobility

Number of Pages Required

2 page

Font styles to use
Sans Serif

Requirements
Must have
• Based on Wordpress, and the designer should be able to implement it on Wordpress on a later step

```html
<!DOCTYPE html>
<html lang="de">
<head>
<meta charset="utf-8">
<title>tanu-werk – Ladelösungen</title>
<link href="https://fonts.googleapis.com/css2?family=Audiowide&family=Roboto:wght@400;500;700&display=swap" rel="stylesheet">
<style>
:root{
  --bg:#111827;
  --bg-foot:#0f1521;
  --pink:#e8159c;
  --violet:#7a4fd6;
  --violet-soft:#8a5fe0;
  --link:#b54fe0;
  --white:#ffffff;
  --text:#e8e8f0;
}
*{box-sizing:border-box;margin:0;padding:0}
html,body{width:1200px;height:2366px;overflow:hidden;background:var(--bg);font-family:'Roboto',sans-serif;color:var(--white)}
.page{position:relative;width:1200px;height:2366px}
.header{position:absolute;top:0;left:0;width:1200px;height:94px;background:var(--bg);display:flex;align-items:center;padding:0 112px;z-index:3}
.brand{display:flex;align-items:center;gap:10px;font-family:'Roboto',sans-serif;font-size:26px;font-weight:500;color:var(--white);width:330px}
.brand-dot{width:18px;height:18px;border-radius:50%;background:var(--pink)}
.nav{display:flex;gap:31px;font-size:16px;font-weight:500;margin-left:0}
.nav a{color:var(--white);text-decoration:none}
.nav a.active{color:var(--pink)}
.social{display:flex;gap:6px;margin-left:auto}
.social span{width:36px;height:36px;border-radius:50%;border:2px solid var(--violet)}
.social span.filled{background:linear-gradient(135deg,var(--pink),var(--violet));border-color:transparent}
.hero{position:absolute;top:94px;left:0;width:1200px;height:680px;overflow:hidden}
.hero-photo{position:absolute;inset:0;background:linear-gradient(110deg,#e78ad8 0%,#c26ad8 35%,#8d5be0 60%,#4f5fe0 85%,#3a4fd0 100%)}
.hero-wave{position:absolute;left:0;top:0}
.hero-content{position:absolute;top:100px;left:160px;width:880px;text-align:center}
.hero-title{font-family:'Audiowide',sans-serif;font-size:36px;letter-spacing:1px;margin-bottom:28px}
.hero-text{font-size:17px;font-weight:700;line-height:27.5px;margin-bottom:14px}
.btn{display:inline-block;margin-top:26px;background:var(--white);color:#9a3fd0;font-size:13px;font-weight:700;padding:17px 30px;border-radius:26px}
.arrow{position:absolute;top:358px;width:36px;height:36px;border-radius:50%;border:2px solid var(--white);display:flex;align-items:center;justify-content:center}
.arrow.next{background:var(--white)}
.intro{position:absolute;top:788px;left:0;width:1200px;text-align:center;font-family:'Audiowide',sans-serif;font-size:26px;line-height:37px}
.cards{position:absolute;top:906px;left:112px;display:flex;gap:23px}
.card{width:310px;height:1046px;border:3px solid;border-image:linear-gradient(180deg,var(--pink),var(--violet)) 1;border-radius:6px;padding:30px 16px 22px;display:flex;flex-direction:column}
.card-icon{width:64px;height:62px;border-radius:6px;background:linear-gradient(135deg,var(--pink),var(--violet));opacity:.85;margin-bottom:26px}
.card-title{font-size:20px;font-weight:500;margin-bottom:14px}
.list{list-style:none;font-size:14px;line-height:22.3px;color:var(--text)}
.list li{position:relative;padding-left:31px;margin-bottom:11px}
.list li::before{content:"";position:absolute;left:0;top:5px;width:12px;height:12px;border-radius:50%;background:var(--violet-soft)}
.list li::after{content:"";position:absolute;left:3px;top:9px;width:3px;height:3px;border-top:1.5px solid var(--bg);border-right:1.5px solid var(--bg);transform:rotate(45deg)}
.list li.sub{font-size:13px;line-height:22px;margin-bottom:2px}
.list li.sub::before{content:"»";background:none;color:var(--pink);top:-1px;width:auto;height:auto;font-size:13px}
.list li.sub::after{display:none}
.list li.sub.last{margin-bottom:11px}
.more{margin-top:auto;font-size:14px;font-weight:700;color:var(--link);display:flex;align-items:center;gap:10px}
.more i{width:12px;height:12px;border-radius:50%;background:var(--violet-soft)}
.footer{position:absolute;top:2045px;left:0;width:1200px;height:321px;background:var(--bg-foot);text-align:center}
.footer-brand{margin-top:78px;display:inline-flex;align-items:center;gap:12px;font-size:38px;font-weight:500}
.footer-brand .brand-dot{width:26px;height:26px}
.footer-links{margin-top:34px;font-size:19px;font-weight:500;word-spacing:2px}
.footer-links span{margin:0 17px}
.footer .social{justify-content:center;margin:18px 0 0}
.footer-rule{position:absolute;left:112px;right:112px;top:271px;border-top:1px solid #2b3244}
.copy{position:absolute;top:290px;left:0;width:1200px;font-size:14px}
.copy b{font-weight:500}
.code{position:absolute;right:47px;top:291px;font-size:12px}
</style>
</head>
<body>
<div class="page">
  <header class="header">
    <div class="brand"><span class="brand-dot"></span>tanu-werk.de</div>
    <nav class="nav">
      <a class="active">Lösungen</a><a>Unternehmen</a><a>Services</a><a>Karriere</a><a>Kontakt</a>
    </nav>
    <div class="social"><span class="filled"></span><span></span><span></span></div>
  </header>

  <section class="hero">
    <div class="hero-photo" role="img" aria-label="Foto eines E-Autos beim Laden an einer Ladesäule in Pink- und Blautönen"></div>
    <svg class="hero-wave" width="1200" height="680" viewBox="0 0 1200 680">
      <path d="M0 680 L0 555 C120 640 220 640 380 610 C600 565 780 500 1000 520 C1110 530 1170 600 1200 640 L1200 680 Z" fill="#111827"/>
      <path d="M0 555 C120 640 220 640 380 610 C600 565 780 500 1000 520 C1110 530 1170 600 1200 640" fill="none" stroke="#e8159c" stroke-width="6"/>
    </svg>
    <div class="hero-content">
      <h1 class="hero-title">TANU-WERK IST IHR PARTNER</h1>
      <p class="hero-text">wenn das Laden nicht nur einfach, sondern die Umsetzung auch aus einer Hand kommen soll. Wir bieten Lösungen sowohl für Privatkunden, Geschäftskunden als auch Kommunen an, die schnell, fair und ohne Eigenleistung zu einer smarten Ladelösung für E-Fahrzeuge kommen möchten.</p>
      <p class="hero-text">Von der Beratung, über die Installation, Inbetriebnahme bis zur Abrechnung und Wartung bekommen Sie bei tanu-werk alles aus einer Hand. Auf Wunsch vermieten wir auch die Ladetechnik und übernehmen im gewerblichen Bereich die direkte Abrechnung mit dem Nutzer. Für Kommunen bieten wir den kostenfreien Full-Service an und beteiligen die Gemeinden an der Nutzung der Infrastruktur.</p>
      <span class="btn">LOSLEGEN</span>
    </div>
    <div class="arrow prev" style="left:40px"><svg width="12" height="12" viewBox="0 0 12 12"><path d="M8 1 L3 6 L8 11" fill="none" stroke="#fff" stroke-width="2"/></svg></div>
    <div class="arrow next" style="left:1124px"><svg width="12" height="12" viewBox="0 0 12 12"><path d="M4 1 L9 6 L4 11" fill="none" stroke="#7a4fd6" stroke-width="2"/></svg></div>
  </section>

  <h2 class="intro">FRAGEN SIE UNS NACH DER AUF IHRE INDIVIDUELLEN<br>BEDÜRFNISSE ZUGESCHNITTENEN LÖSUNG:</h2>

  <div class="cards">
    <article class="card">
      <div class="card-icon" role="img" aria-label="Symbol: Person in schützenden Händen"></div>
      <h3 class="card-title">ALS PRIVATKUNDE</h3>
      <ul class="list">
        <li>Bestandsanalyse mit umfangreicher Beratung über die Möglichkeiten der Umsetzung</li>
        <li>Inbetriebnahme und Einweisung in die Ladetechnik</li>
        <li>Reparaturservice, unter Berücksichtigung der geltenden Garantie Ansprüche</li>
        <li>Prüfung und Übernahme der Anmeldung verfügbarer Fördermöglichkeiten</li>
        <li>Jährlich technische Wartung nach DGUV3</li>
        <li>Installation inkl. aller notwendigen Materialien und Tätigkeiten (Durchbrüche, Erdarbeiten, etc.</li>
        <li>Inbetriebnahme und Einweisung in die Ladetechnik</li>
        <li>Jährlich technische Wartung nach DGUV3</li>
        <li>Reparaturservice, unter Berücksichtigung der geltenden Garantie Ansprüche</li>
      </ul>
      <div class="more">MEHR ERFAHREN <i></i></div>
    </article>
    <article class="card">
      <div class="card-icon" role="img" aria-label="Symbol: Handschlag mit Münze"></div>
      <h3 class="card-title">ALS GESCHÄFTSKUNDE</h3>
      <ul class="list">
        <li>Durchführung einer individuellen Bedarfsanalyse inkl. Ermittlung der Anforderungen für:</li>
        <li class="sub">Haus- und Immobilienverwaltungen</li>
        <li class="sub">Dienstleistungs- und Handelsunternehmen</li>
        <li class="sub">Hotel und Beherbergungsbetriebe</li>
        <li class="sub">Parkraum- und Parkhausbetreiber</li>
        <li class="sub last">Tourismus, Sport- und Freizeiteinrichtungen</li>
        <li>Planung und Projektierung des Installationsaufwands inkl. Materialverbrauch</li>
        <li>Leasing oder Kauf der Hardware</li>
        <li>Normgerechte Installation der Ladeinfrastruktur inkl. Durchbruch-, Brandschutz- und Erdarbeiten</li>
        <li>Bei Bestandsbauten Integration der Ladeinfrastruktur in die Gebäudesystemtechnik und ggf. Anpassung des Netzanschlusses</li>
        <li>ODER direkte Abrechnung mit den Nutzern</li>
        <li class="sub">Parkraum- und Parkhausbetreiber</li>
        <li class="sub last">Tourismus, Sport- und Freizeiteinrichtungen</li>
        <li style="margin-bottom:2px">Wiederkehrende technische Prüfung der Anlage nach DGUV 3</li>
        <li style="margin-bottom:4px">Unterstützung bei der mtl. Nutzungsabrechnung und Einbindung in Ihre vorhandene Abrechnungssysteme</li>
        <li style="margin-bottom:4px">Planung und Projektierung des Installationsaufwands inkl.</li>
        <li>Leasing oder Kauf der Hardware</li>
      </ul>
      <div class="more">MEHR ERFAHREN <i></i></div>
    </article>
    <article class="card">
      <div class="card-icon" role="img" aria-label="Symbol: Rathausgebäude"></div>
      <h3 class="card-title">ALS KOMMUNE</h3>
      <ul class="list">
        <li>Konzeptionierung möglicher Ladeinfrastrukturen innerhalb Ihrer Gemeinde</li>
        <li>Fachgerechte Installation und Inbetriebnahme</li>
        <li>Regelmäßige Wartung gemäß Vorschrif</li>
        <li>Reparatur und Kundenservice</li>
        <li>Planung und Projektsteuerung inkl. sämtlicher behördlicher Genehmigungsverfahren und Beantragung von Fördermitteln</li>
        <li>Direkte Abrechnung mit dem Nutzer</li>
        <li>Beteiligung der Gemeinde am Umsatz</li>
        <li>Möglichkeit der Integration von Bonusprogrammen, mit denen der lokale Einzelhandel beworben wird</li>
        <li style="margin-bottom:7px">von Fördermitteln</li>
        <li>Fachgerechte Installation und Inbetriebnahme</li>
        <li style="margin-bottom:7px">Regelmäßige Wartung gemäß Vorschrif</li>
        <li style="margin-bottom:8px">Reparatur und Kundenservice</li>
        <li style="margin-bottom:8px">Direkte Abrechnung mit dem Nutzer</li>
        <li style="margin-bottom:7px">Beteiligung der Gemeinde am Umsatz</li>
        <li>Möglichkeit der Integration von Bonusprogrammen, mit denen der lokale Einzelhandel beworben wird</li>
      </ul>
      <div class="more">MEHR ERFAHREN <i></i></div>
    </article>
  </div>

  <footer class="footer">
    <div class="footer-brand"><span class="brand-dot"></span>tanu-werk.de</div>
    <div class="footer-links">AGB<span>|</span>DATENSCHUTZERKLARUNG<span>|</span>IMPRESSUM<span>|</span>KONTAKT<span>|</span>KARRIERE<span>|</span>FAQS</div>
    <div class="social"><span class="filled"></span><span></span><span></span></div>
    <div class="footer-rule"></div>
    <p class="copy">© <b>tanu-werk GmbH</b> &nbsp;|&nbsp; All Rights Reserved</p>
    <span class="code">C45</span>
  </footer>
</div>
</body>
</html>
```